Surgical Device Brochure for New surgical wound care product (Veltrina)

Four page brochure for surgical device (8.5 x 11). The purpose of this flyer is convince hospital adminstrators and surgeons that Veltrina will save hospitals millions of dollars each year while saving lives and improving patient care.

Use the provided text in the attached document which has the main points. the last page should be space for people to take notes and perform their own calculations. On page 3, please highlight the questions we ask which will help them figure out how much money our product will save them. page 1 and 2 should cover the main points in the document, have quotes, and interesting graphics and layout.

Target Market(s)

Hospital Administrators and Surgeons (medical doctors) and financial controllers

Industry/Entity Type

Medical

Font styles to use
Serif

Colors
85abd2
b7a5cd
fbee3e
e667a6

Requirements
Must have
• Four pages, last page has caption at top with space for notes.
• Emphasis on hospital cost control
Nice to have
• Nice graphics of surgeons, surgery centers, emergency rooms, and surgical tools and graphs showing profits going up and costs going down
• dynamic, exciting, high-tech, clean, organized.
Should not have
• too much red. text that is too small.

```html
<!DOCTYPE html>
<html lang="en">
<head>
<meta charset="utf-8">
<title>Veltrina Brochure Spread</title>
<link href="https://fonts.googleapis.com/css2?family=Josefin+Sans:wght@400;600&family=Open+Sans:wght@400;600;700;800&display=swap" rel="stylesheet">
<style>
  :root{
    --teal:#169c8f;
    --teal-dark:#0f7f74;
    --teal-line:#b9dcd8;
    --paper:#ffffff;
    --paper-left:#f1f2f2;
    --bg:#dcdcdc;
    --ink:#5a6163;
    --photo-a:#1c6f68;
    --photo-b:#7fa8a8;
    --photo-c:#d9e2e3;
  }
  *{margin:0;padding:0;box-sizing:border-box}
  html,body{width:1200px;height:900px;overflow:hidden;background:var(--bg);font-family:"Open Sans",sans-serif}
  .spread{position:absolute;left:28px;top:80px;width:1144px;height:740px;display:flex;box-shadow:0 8px 24px rgba(0,0,0,.12)}
  .page{position:relative;width:572px;height:740px}
  .page--notes{background:var(--paper-left)}
  .page--intro{background:var(--paper)}

  .calc-head{position:absolute;left:42px;top:40px;display:flex;align-items:center;gap:12px}
  .calc-head__title{color:var(--teal);font-weight:800;font-size:15px;letter-spacing:.3px;line-height:1}
  .calc-head__sub{color:var(--ink);font-size:9px;letter-spacing:.4px;margin-top:3px}
  .notes-label{position:absolute;left:60px;top:112px;color:var(--teal);font-size:9px;opacity:.8}
  .notes-lines{position:absolute;left:60px;right:60px;top:130px}
  .notes-lines span{display:block;height:15.6px;border-bottom:1px solid var(--teal-line)}

  .contact-band{position:absolute;left:0;right:0;bottom:0;height:170px;background:var(--teal);color:#fff;text-align:center;padding-top:30px}
  .wordmark{font-family:"Josefin Sans",sans-serif;font-weight:600;letter-spacing:1.5px;line-height:1}
  .contact-band .wordmark{font-size:22px;color:#fff}
  .tagline{font-size:7px;margin-top:4px}
  .contact-band__head{font-size:7.5px;font-weight:700;margin-top:22px;letter-spacing:.3px}
  .contact-band__line{font-size:7px;margin-top:6px;opacity:.9}
  .contact-band__web{font-size:7px;margin-top:8px;opacity:.9}

  .page--intro .brand{position:absolute;top:92px;left:0;right:0;text-align:center}
  .page--intro .wordmark{font-size:34px;color:var(--teal)}
  .page--intro .tagline{color:var(--teal-dark);font-weight:600;font-size:8px}
  .photo-accent{position:absolute;left:64px;right:44px;top:180px;height:36px;background:var(--teal)}
  .photo{position:absolute;left:44px;right:64px;top:190px;height:300px;background:linear-gradient(135deg,var(--photo-a) 0%,var(--photo-b) 55%,var(--photo-c) 100%)}
  .facts{position:absolute;left:44px;right:44px;top:470px;height:190px;background:var(--teal);color:#fff;padding:26px 28px;font-size:10px;line-height:1.45}
  .facts p{margin-bottom:8px}
  .facts strong{font-weight:800}
  .site{position:absolute;bottom:34px;left:0;right:0;text-align:center;color:var(--teal);font-size:8px}
</style>
</head>
<body>
<main class="spread">
  <section class="page page--notes">
    <header class="calc-head">
      <svg width="34" height="34" viewBox="0 0 34 34" fill="none" stroke="#169c8f" stroke-width="1.6" aria-hidden="true">
        <rect x="2" y="2" width="18" height="24" rx="2"/>
        <rect x="5" y="5" width="12" height="5"/>
        <path d="M5 14h3M10 14h3M15 14h2M5 18h3M10 18h3M5 22h3M10 22h3"/>
        <circle cx="24" cy="23" r="8" fill="#f1f2f2"/>
        <path d="M26.5 19.5h-3.5a2 2 0 0 0 0 4h2a2 2 0 0 1 0 4h-3.5M24 17.5v2M24 27.5v2"/>
      </svg>
      <div>
        <div class="calc-head__title">CALCULATE</div>
        <div class="calc-head__sub">YOUR TOTAL ANNUAL COST</div>
      </div>
    </header>
    <div class="notes-label">Notes :</div>
    <div class="notes-lines">
      <span></span><span></span><span></span><span></span><span></span><span></span><span></span><span></span>
      <span></span><span></span><span></span><span></span><span></span><span></span><span></span><span></span>
      <span></span><span></span><span></span><span></span><span></span><span></span><span></span><span></span>
      <span></span><span></span>
    </div>
    <footer class="contact-band">
      <div class="wordmark">VELTRINA</div>
      <div class="tagline">Close with Veltrina</div>
      <div class="contact-band__head">FOR PRODUCT INQUIRIES AND PURCHASES, PLEASE CONTACT US:</div>
      <div class="contact-band__line">info@veltrinamed.com | Product information &amp; inquiries | (555) 201-3820</div>
      <div class="contact-band__web">www.veltrinaclose.com</div>
    </footer>
  </section>

  <section class="page page--intro">
    <div class="brand">
      <div class="wordmark">VELTRINA</div>
      <div class="tagline">Close with Veltrina</div>
    </div>
    <div class="photo-accent"></div>
    <div class="photo" role="img" aria-label="Surgical team in green gowns and masks operating in a theatre, with inset of surgical instruments"></div>
    <div class="facts">
      <p>In 2016, the Federal Government increased Medicare penalties to $528 million, which currently impacts 2,597 hospitals with an average amount of $203,000 per facility. (Dana Merrit, August 4, 2016, Harbor Health Journal, healthwire.org)</p>
      <p>Surgical Site Infection costs hospitals between <strong>$11,000</strong> to <strong>$35,000</strong> for each case of infection.</p>
      <p>Calder State Dept. of Health "Surgical Site Infection (SSI) continues to represent a significant portion of healthcare associated infections." - National Health Services Office.</p>
      <p>Hospitals that reduce their Surgical Site Infection rate stand to <strong>save</strong> an estimated <strong>$1</strong> to <strong>$2 million per year</strong> annual SSI Related Cost savings. - Calder State Dept. of Health</p>
    </div>
    <div class="site">www.veltrinaclose.com</div>
  </section>
</main>
</body>
</html>
```